Build a landing page to promote a service (dialler consultation and support).

We are a call centre consultation firm and we need a landing page to promote a service. The service is Tormalux dialler consultation and support.
If you do not know what Tormalux is, please do some quick "Zorvex" research for more information.
The landing page will be promoted with a paid advertisement, so we want something that is simple, and explains exactly what service we offer.
There are two objectives for the landing page:
1) A "call to action" which directs the user to a contact page, including a form plus all of our contact details.
2) A form for them viewers to enter their details to get a "FREE" quote for their project. This form should be placed on the main page.
Notes:
The call to action will require the viewer to enter their name, email, phone number as well as a description of their request. There will also need to be a drop down menu for the type of quote. This menu should have the following options:
1) Tormalux support
2) Tormalux hosting
3) Tormalux customisation
4) Other
We need 2 pages in total:
1) Main landing page
This is the home page. It will need to clearly indicate our services and our key selling features.
Services:
* Tormalux support
* Tormalux hosting
* Tormalux customisation
Key Selling Features:
* Australian based
* PCI complaint
* 10+ years of dialler and call centre experience
* we run a sister company which is a highly reputable 40 seat call centre, so we know first hand about call centre technology.
The main landing page will have an "about us" section with a few paragraphs about how we got started.
-------------------------------------------------------------------------
2) Contact page
All of our contact details will live on this page, as well as a contact form.
Other notes:
We will be self hosting the landing page.
We already have a domain name.
The design must be clean and incorporate our logo, as well as it's colours. (Logo attached)
We want a fully function HTML landing page, not just a "PSD" design.
The page must be mobile optimised.
Anyone using Tormalux software.

```html
<!DOCTYPE html>
<html lang="en">
<head>
<meta charset="utf-8">
<title>Quillcall – Tormalux dialler consultation and support</title>
<link href="https://fonts.googleapis.com/css2?family=Poppins:wght@400;500;600&family=Open+Sans:wght@400;600;700&display=swap" rel="stylesheet">
<style>
:root{
  --backdrop:#eeeeee;
  --white:#ffffff;
  --ink:#1f2428;
  --body:#6b7177;
  --teal:#1fb39a;
  --blue:#1b7cc4;
  --navy:#2a64a8;
  --mist:#e9eef2;
  --line:#d5dadf;
  --card-back:#dfe4e8;
}
*{box-sizing:border-box;margin:0;padding:0}
html,body{width:1200px;height:4380px;overflow:hidden}
body{background:var(--backdrop);font-family:"Open Sans",Arial,sans-serif;color:var(--body);position:relative}
.page{position:absolute;left:123px;width:952px;background:var(--white);box-shadow:0 2px 10px rgba(0,0,0,.08)}
.page--home{top:111px;height:2984px}
.page--contact{top:3197px;height:1072px}
section,header,footer{position:relative;width:952px}
h1,h2,h3{font-family:"Poppins",Arial,sans-serif;color:var(--ink)}

/* header */
.site-header{height:93px;background:var(--white)}
.brand{position:absolute;left:108px;top:4px;width:80px;text-align:center}
.brand__dot{display:block;width:50px;height:50px;border-radius:50%;background:var(--blue);margin:0 auto}
.brand__name{display:block;font-family:"Poppins",Arial,sans-serif;font-weight:500;font-size:24px;color:var(--blue);line-height:30px;margin-left:-20px;margin-right:-20px}
.topbar{position:absolute;right:76px;top:14px;font-size:12px;color:var(--ink);display:flex;gap:10px;align-items:center}
.topbar svg{width:11px;height:11px;vertical-align:-1px;margin-right:4px}
.topbar .sep{width:1px;height:12px;background:var(--ink)}
.nav{position:absolute;left:388px;top:50px;display:flex;align-items:center;gap:26px;font-size:13px;color:var(--ink)}
.nav .is-active{color:var(--teal)}
.nav svg{width:13px;height:13px}
.nav__cta{position:absolute;left:782px;top:45px;width:94px;height:30px;border:1.5px solid var(--teal);border-radius:15px;color:var(--teal);font-size:10px;font-weight:600;text-align:center;line-height:27px;text-transform:uppercase}

/* hero */
.hero{overflow:hidden}
.hero__photo{position:absolute;inset:0;background:linear-gradient(100deg,#2b2c2d 0%,#4a4641 35%,#8f8070 62%,#6d6153 80%,#3e3a35 100%)}
.hero__shade{position:absolute;inset:0;background:linear-gradient(90deg,rgba(0,0,0,.35),rgba(0,0,0,0) 60%)}
.hero__title{position:absolute;left:78px;color:var(--white);font-weight:500;font-size:54px;line-height:64px}
.btn{display:inline-block;border-radius:24px;font-size:11px;font-weight:700;text-transform:uppercase;text-align:center;letter-spacing:.3px}
.btn--ghost-light{border:2px solid var(--white);color:var(--white)}
.btn--ghost-teal{border:1.5px solid var(--teal);color:var(--teal)}
.btn--solid{background:var(--teal);color:var(--white)}
.hero .btn{position:absolute;left:78px;width:160px;height:46px;line-height:42px}
.dots{position:absolute;left:50%;transform:translateX(-50%);display:flex;gap:5px}
.dots i{width:9px;height:9px;border-radius:50%;border:1.5px solid var(--white)}
.dots i:first-child{background:var(--white)}
.hero--home{height:450px}
.hero--home .hero__title{top:86px}
.hero--home .btn{top:304px}
.hero--home .dots{top:390px}
.hero--contact{height:281px}
.hero--contact .hero__title{top:102px}
.hero--contact .dots{top:220px}

/* welcome */
.welcome{height:543px;text-align:center}
.section-title{font-size:34px;font-weight:500;color:var(--ink)}
.welcome .section-title{position:absolute;top:66px;width:100%}
.welcome__intro{position:absolute;top:126px;left:176px;width:600px;font-size:12px;line-height:20px}
.service{position:absolute;top:237px;width:234px;height:233px}
.service__back{position:absolute;left:10px;top:-8px;width:234px;height:233px;background:var(--card-back)}
.service__card{position:absolute;inset:0;background:#f4f6f7;padding:44px 22px 0}
.service__card svg{width:40px;height:36px;display:block;margin:0 auto 12px}
.service__card h3{font-size:17px;font-weight:500;margin-bottom:10px}
.service__card p{font-size:11px;line-height:17px}
.service__more{display:block;margin-top:14px;color:var(--teal);font-size:10px;font-weight:700;text-transform:uppercase}

/* features */
.features{height:447px;background:var(--mist);text-align:center}
.features .section-title{position:absolute;top:58px;width:100%}
.features__row{position:absolute;left:0;top:0;width:952px;height:447px}
.feature-text{position:absolute;font-size:14px;line-height:21px;color:var(--ink);text-align:center;display:flex;align-items:center;justify-content:center}

/* about */
.about{height:511px}
.about__photo{position:absolute;left:0;top:0;width:414px;height:359px;background:linear-gradient(135deg,#d9dde0 0%,#a8b4bd 40%,#4f6a80 70%,#2d3640 100%)}
.about__box{position:absolute;left:362px;top:64px;width:511px;height:374px;border:1px solid var(--line)}
.about__content{position:absolute;left:450px;top:104px;width:400px}
.about__content h2{font-size:32px;font-weight:500;margin-bottom:16px}
.about__content p{font-size:11.5px;line-height:20px}
.about__content .btn{margin-top:30px;width:116px;height:38px;line-height:35px;font-size:10px}

/* story */
.story{height:277px;background:var(--blue);text-align:center;color:var(--white)}
.story h2{position:absolute;top:40px;width:100%;color:var(--white);font-size:32px;font-weight:500}
.story p{position:absolute;top:100px;left:146px;width:660px;font-size:11.5px;line-height:19px}
.story .btn{position:absolute;top:170px;left:406px;width:140px;height:40px;line-height:36px}

/* quote */
.quote{height:421px}
.quote__panel{position:absolute;left:0;top:0;width:481px;height:421px;background:#f0f3f5}
.quote__photo{position:absolute;left:481px;top:0;width:471px;height:421px;background:linear-gradient(160deg,#cfc9c0 0%,#a79d90 35%,#4c4d50 65%,#8f8478 100%)}
.quote-form{position:absolute;left:75px;top:44px;width:370px}
.quote-form h2{font-size:32px;font-weight:500;margin-bottom:20px;line-height:44px}
.field-row{display:flex;gap:10px;margin-bottom:8px}
.field{flex:1;height:34px;border:1px solid var(--line);background:var(--white);font-size:10.5px;color:var(--body);padding:0 8px;line-height:32px;position:relative}
.field--select svg{position:absolute;right:10px;top:14px;width:8px;height:5px}
.field--message{height:64px;line-height:28px}
.quote-form .btn{margin-top:14px;width:100px;height:34px;line-height:34px}

/* footer */
.site-footer{text-align:center;font-size:11px;color:var(--body)}
.social{position:absolute;left:0;width:100%;display:flex;justify-content:center;gap:10px}
.social i{width:34px;height:34px;border-radius:50%;border:1.5px solid var(--navy)}
.footer__contact{position:absolute;width:100%;display:flex;justify-content:center;gap:10px;align-items:center}
.footer__contact svg{width:10px;height:10px;vertical-align:-1px;margin-right:3px}
.footer__contact .sep,.footer__links .sep{width:1px;height:11px;background:var(--body)}
.footer__links{position:absolute;width:100%;display:flex;justify-content:center;gap:10px;align-items:center}
.footer__copy{position:absolute;width:100%}
.page--home .site-footer{height:242px}
.page--home .social{top:62px}
.page--home .footer__contact{top:129px}
.page--home .footer__links{top:161px}
.page--home .footer__copy{top:190px}

/* contact */
.contact{height:450px;border-bottom:1px solid var(--line);margin:0 76px;width:800px}
.contact .quote-form{left:0;top:62px}
.contact__map{position:absolute;left:414px;top:73px;width:386px;height:327px;background:linear-gradient(135deg,#c9dff0 0%,#b7d3ea 45%,#e4e6df 60%,#d9dbd2 100%)}
.page--contact .site-footer{height:248px}
.page--contact .social{top:62px}
.page--contact .footer__contact{top:126px}
.page--contact .footer__links{top:158px}
.page--contact .footer__copy{top:187px}
</style>
</head>
<body>

<main class="page page--home">
  <header class="site-header">
    <div class="brand"><span class="brand__dot"></span><span class="brand__name">Quillcall</span></div>
    <div class="topbar">
      <span><svg viewBox="0 0 24 24" fill="#1fb39a"><path d="M6.6 10.8a15 15 0 0 0 6.6 6.6l2.2-2.2c.3-.3.7-.4 1-.2 1.1.4 2.3.6 3.6.6.6 0 1 .4 1 1V20c0 .6-.4 1-1 1A17 17 0 0 1 3 4c0-.6.4-1 1-1h3.5c.6 0 1 .4 1 1 0 1.3.2 2.5.6 3.6.1.3 0 .7-.2 1z"/></svg>1 800 555 0142</span>
      <span class="sep"></span>
      <span><svg viewBox="0 0 24 24" fill="#1fb39a"><path d="M2 5h20v14H2z"/><path d="M2 5l10 8 10-8" stroke="#fff" stroke-width="2" fill="none"/></svg>info@quillcall.com</span>
    </div>
    <nav class="nav"><span class="is-active">Home</span><span>About</span><span>Services</span><span>Features</span><span>Blog</span><svg viewBox="0 0 24 24" fill="none" stroke="#1f2428" stroke-width="3"><circle cx="10" cy="10" r="7"/><path d="M15 15l7 7"/></svg></nav>
    <span class="nav__cta">Contact us</span>
  </header>

  <section class="hero hero--home">
    <div class="hero__photo" role="img" aria-label="Photo of a call centre agent wearing a headset in a bright office"></div>
    <div class="hero__shade"></div>
    <h1 class="hero__title">Tormalux dialler<br>consultation<br>and support</h1>
    <span class="btn btn--ghost-light">Get a free quote</span>
    <div class="dots"><i></i><i></i><i></i><i></i></div>
  </section>

  <section class="welcome">
    <h2 class="section-title">Welcome to Quillcall</h2>
    <p class="welcome__intro">We help contact centres run dialler platforms that stay fast, stable and secure. From first install to daily tuning, our team handles the technical side so your agents can keep talking to customers and your managers can focus on results.</p>

    <article class="service" style="left:76px">
      <div class="service__back"></div>
      <div class="service__card">
        <svg viewBox="0 0 40 36" fill="none" stroke="#1b7cc4" stroke-width="3.5"><path d="M6 22v-4a14 14 0 0 1 28 0v4"/><rect x="4" y="20" width="7" height="11" rx="2" fill="#1b7cc4"/><rect x="29" y="20" width="7" height="11" rx="2" fill="#1b7cc4"/></svg>
        <h3>Tormalux Support</h3>
        <p>Fast help from engineers who know every setting and fix issues quickly.</p>
        <span class="service__more">Read more</span>
      </div>
    </article>
    <article class="service" style="left:353px">
      <div class="service__back"></div>
      <div class="service__card">
        <svg viewBox="0 0 40 36" fill="#1b7cc4"><ellipse cx="20" cy="6" rx="13" ry="4.5"/><path d="M7 9c0 3 26 3 26 0v6c0 3-26 3-26 0z"/><path d="M7 18c0 3 26 3 26 0v6c0 3-26 3-26 0z"/><path d="M7 27c0 3 26 3 26 0v3c0 4-26 4-26 0z"/></svg>
        <h3>Tormalux Hosting</h3>
        <p>Secure servers tuned for dialling, monitored around the clock by our team.</p>
        <span class="service__more">Read more</span>
      </div>
    </article>
    <article class="service" style="left:630px">
      <div class="service__back"></div>
      <div class="service__card">
        <svg viewBox="0 0 40 36" fill="#1b7cc4"><circle cx="20" cy="9" r="6"/><path d="M10 30c0-7 4-12 10-12s10 5 10 12z"/><circle cx="8" cy="13" r="4.5"/><path d="M0 30c0-5 3-9 8-9 1.5 0 2.5.3 3.5.8C9.5 24 8.5 27 8.5 30z"/><circle cx="32" cy="13" r="4.5"/><path d="M40 30c0-5-3-9-8-9-1.5 0-2.5.3-3.5.8 2 2.2 3 5.2 3 8.2z"/></svg>
        <h3>Tormalux Customisation</h3>
        <p>Custom scripts, reports and workflows built to match the way you work.</p>
        <span class="service__more">Read more</span>
      </div>
    </article>
  </section>

  <section class="features">
    <h2 class="section-title">Key Selling Features</h2>
    <svg class="features__row" viewBox="0 0 952 447">
      <line x1="102" y1="263" x2="849" y2="263" stroke="#1fb39a" stroke-width="1.5"/>
      <circle cx="169" cy="263" r="66" fill="#fff" stroke="#2a64a8" stroke-width="3"/>
      <circle cx="344" cy="263" r="110" fill="#fff" stroke="#1fb39a" stroke-width="1.5"/>
      <circle cx="607" cy="263" r="110" fill="#fff" stroke="#1fb39a" stroke-width="1.5"/>
      <circle cx="476" cy="263" r="35" fill="#fff" stroke="#1fb39a" stroke-width="4"/>
      <circle cx="476" cy="263" r="24" fill="#1fb39a"/>
      <circle cx="782" cy="263" r="66" fill="#fff" stroke="#2a64a8" stroke-width="3"/>
    </svg>
    <div class="feature-text" style="left:119px;top:213px;width:100px;height:100px">Australian based</div>
    <div class="feature-text" style="left:264px;top:203px;width:150px;height:120px">10+ years of<br>dialler and call<br>centre experience</div>
    <div class="feature-text" style="left:522px;top:173px;width:172px;height:180px">we run a sister company which is a highly reputable 40 seat call centre, so we know first hand about call centre technology.</div>
    <div class="feature-text" style="left:732px;top:213px;width:100px;height:100px">PCI<br>complaint</div>
  </section>

  <section class="about">
    <div class="about__photo" role="img" aria-label="Photo of a manager helping a seated agent at a computer"></div>
    <div class="about__box"></div>
    <div class="about__content">
      <h2>About us</h2>
      <p>We started as call centre operators ourselves, running outbound campaigns on open source diallers. Over the years we learned what keeps a floor productive and what slows it down. That know-how became a consultancy that now supports teams across Australia with setup, hosting and custom development. We still run our own contact centre, so every change we suggest has been tested on a real floor first.</p>
      <span class="btn btn--ghost-teal">Read more</span>
    </div>
  </section>

  <section class="story">
    <h2>How we got started</h2>
    <p>What began as a fix for our own dialler grew into a service for other centres. Today we help teams of every size get more from their platform.</p>
    <span class="btn btn--ghost-light">Get started</span>
  </section>

  <section class="quote">
    <div class="quote__panel"></div>
    <div class="quote__photo" role="img" aria-label="Photo of hands typing on a laptop beside a coffee cup"></div>
    <form class="quote-form">
      <h2>Get a FREE quote</h2>
      <div class="field-row"><span class="field">First Name</span><span class="field">Last Name</span></div>
      <div class="field-row"><span class="field">Email Address</span><span class="field">Phone Number</span></div>
      <div class="field-row"><span class="field field--select">Select Services<svg viewBox="0 0 8 5"><path d="M0 0h8L4 5z" fill="#1f2428"/></svg></span></div>
      <div class="field-row"><span class="field field--message">Message</span></div>
      <span class="btn btn--solid">Submit</span>
    </form>
  </section>

  <footer class="site-footer">
    <div class="social"><i></i><i></i><i></i><i></i></div>
    <div class="footer__contact">
      <span><svg viewBox="0 0 24 24" fill="#2a64a8"><path d="M12 2a7 7 0 0 0-7 7c0 5 7 13 7 13s7-8 7-13a7 7 0 0 0-7-7zm0 9.5A2.5 2.5 0 1 1 12 6.5a2.5 2.5 0 0 1 0 5z"/></svg>48 Fernhill Crescent Lakeview, MO 63000</span>
      <span class="sep"></span>
      <span><svg viewBox="0 0 24 24" fill="#2a64a8"><path d="M6.6 10.8a15 15 0 0 0 6.6 6.6l2.2-2.2c.3-.3.7-.4 1-.2 1.1.4 2.3.6 3.6.6.6 0 1 .4 1 1V20c0 .6-.4 1-1 1A17 17 0 0 1 3 4c0-.6.4-1 1-1h3.5c.6 0 1 .4 1 1 0 1.3.2 2.5.6 3.6.1.3 0 .7-.2 1z"/></svg>1 800 555 0142</span>
      <span class="sep"></span>
      <span><svg viewBox="0 0 24 24" fill="#2a64a8"><path d="M2 5h20v14H2z"/><path d="M2 5l10 8 10-8" stroke="#fff" stroke-width="2" fill="none"/></svg>info@quillcall.com</span>
    </div>
    <div class="footer__links"><span>Help</span><span class="sep"></span><span>FAQ</span><span class="sep"></span><span>Support</span><span class="sep"></span><span>Sitemap</span><span class="sep"></span><span>Terms Of Use</span><span class="sep"></span><span>Privacy Statement</span></div>
    <div class="footer__copy">Quillcall © 2018 All rights reserved.</div>
  </footer>
</main>

<main class="page page--contact">
  <header class="site-header">
    <div class="brand"><span class="brand__dot"></span><span class="brand__name">Quillcall</span></div>
    <div class="topbar">
      <span><svg viewBox="0 0 24 24" fill="#1fb39a"><path d="M6.6 10.8a15 15 0 0 0 6.6 6.6l2.2-2.2c.3-.3.7-.4 1-.2 1.1.4 2.3.6 3.6.6.6 0 1 .4 1 1V20c0 .6-.4 1-1 1A17 17 0 0 1 3 4c0-.6.4-1 1-1h3.5c.6 0 1 .4 1 1 0 1.3.2 2.5.6 3.6.1.3 0 .7-.2 1z"/></svg>1 800 555 0142</span>
      <span class="sep"></span>
      <span><svg viewBox="0 0 24 24" fill="#1fb39a"><path d="M2 5h20v14H2z"/><path d="M2 5l10 8 10-8" stroke="#fff" stroke-width="2" fill="none"/></svg>info@quillcall.com</span>
    </div>
    <nav class="nav"><span>Home</span><span>About</span><span>Services</span><span>Features</span><span>Blog</span><svg viewBox="0 0 24 24" fill="none" stroke="#1f2428" stroke-width="3"><circle cx="10" cy="10" r="7"/><path d="M15 15l7 7"/></svg></nav>
    <span class="nav__cta">Contact us</span>
  </header>

  <section class="hero hero--contact">
    <div class="hero__photo" role="img" aria-label="Photo of a call centre agent wearing a headset in a bright office"></div>
    <div class="hero__shade"></div>
    <h1 class="hero__title">Contact Us</h1>
    <div class="dots"><i></i><i></i><i></i><i></i></div>
  </section>

  <section class="contact">
    <form class="quote-form">
      <h2>Get a FREE quote</h2>
      <div class="field-row"><span class="field">First Name</span><span class="field">Last Name</span></div>
      <div class="field-row"><span class="field">Email Address</span><span class="field">Phone Number</span></div>
      <div class="field-row"><span class="field field--select">Select Services<svg viewBox="0 0 8 5"><path d="M0 0h8L4 5z" fill="#1f2428"/></svg></span></div>
      <div class="field-row"><span class="field field--message">Message</span></div>
      <span class="btn btn--solid">Submit</span>
    </form>
    <div class="contact__map" role="img" aria-label="Map showing the office location beside a lake"></div>
  </section>

  <footer class="site-footer">
    <div class="social"><i></i><i></i><i></i><i></i></div>
    <div class="footer__contact">
      <span><svg viewBox="0 0 24 24" fill="#2a64a8"><path d="M12 2a7 7 0 0 0-7 7c0 5 7 13 7 13s7-8 7-13a7 7 0 0 0-7-7zm0 9.5A2.5 2.5 0 1 1 12 6.5a2.5 2.5 0 0 1 0 5z"/></svg>48 Fernhill Crescent Lakeview, MO 63000</span>
      <span class="sep"></span>
      <span><svg viewBox="0 0 24 24" fill="#2a64a8"><path d="M6.6 10.8a15 15 0 0 0 6.6 6.6l2.2-2.2c.3-.3.7-.4 1-.2 1.1.4 2.3.6 3.6.6.6 0 1 .4 1 1V20c0 .6-.4 1-1 1A17 17 0 0 1 3 4c0-.6.4-1 1-1h3.5c.6 0 1 .4 1 1 0 1.3.2 2.5.6 3.6.1.3 0 .7-.2 1z"/></svg>1 800 555 0142</span>
      <span class="sep"></span>
      <span><svg viewBox="0 0 24 24" fill="#2a64a8"><path d="M2 5h20v14H2z"/><path d="M2 5l10 8 10-8" stroke="#fff" stroke-width="2" fill="none"/></svg>info@quillcall.com</span>
    </div>
    <div class="footer__links"><span>Help</span><span class="sep"></span><span>FAQ</span><span class="sep"></span><span>Support</span><span class="sep"></span><span>Sitemap</span><span class="sep"></span><span>Terms Of Use</span><span class="sep"></span><span>Privacy Statement</span></div>
    <div class="footer__copy">Quillcall © 2018 All rights reserved.</div>
  </footer>
</main>

</body>
</html>
```